Animal Eye Clinic needs a Business card

We are a new veterinary ophthalmology practice (Ridgeline Pet Vision Care) and we need a business card designed. We only see animal eyes - we are not a regular veterinary clinic. We already have a logo. We are looking for a professional, good looking business card to hand out to our clients. We are looking for something simple but professional and contemporary. Our logo is likely the only picture/graphic that needs to be on the card.
Updates

Contact Information for Business Card

Delia Vossman, BSc, DVM, MSc, DipACVO
Veterinary Ophthalmologist

Phone: 250.418.3927
Email: ridgelinepetvisioncare@mailbox-example.net
Website: ridgelinepetvisioncare-example.net
Address: 1874 Thornbury Rd
Kelowna, BC, V1X 4M9

Colors

Designer to choose colors to be used in the design.

Requirements
Must have
• Our logo (attached)

```html
<!DOCTYPE html>
<html lang="en">
<head>
<meta charset="utf-8">
<title>Ridgeline Pet Vision Care – Business Card</title>
<link rel="stylesheet" href="https://fonts.googleapis.com/css2?family=Open+Sans:wght@400;600;700&display=swap">
<style>
  :root {
    --backdrop: #1f1f1f;
    --teal: #0397aa;
    --white: #ffffff;
    --ink: #3a3a3a;
    --muted: #7a7a7a;
    --shadow: rgba(0, 0, 0, 0.55);
  }
  * { box-sizing: border-box; margin: 0; padding: 0; }
  html, body {
    width: 1200px;
    height: 900px;
    overflow: hidden;
    background: var(--backdrop);
    font-family: "Open Sans", Arial, sans-serif;
  }
  .stage { position: relative; width: 1200px; height: 900px; }

  .card {
    position: absolute;
    top: 200px;
    width: 310px;
    height: 502px;
    box-shadow: 3px 4px 6px var(--shadow);
  }
  .card-front {
    left: 253px;
    background: var(--white);
    border-radius: 62px 0 62px 0;
  }
  .card-back {
    left: 627px;
    background: var(--teal);
    border-radius: 0 62px 0 62px;
  }

  /* Brand name stand-in */
  .brand {
    position: absolute;
    display: flex;
    align-items: center;
    gap: 10px;
  }
  .brand-dot {
    flex: none;
    border-radius: 50%;
  }
  .brand-name {
    font-weight: 700;
    text-transform: uppercase;
    line-height: 1.15;
  }
  .card-front .brand { left: 32px; top: 126px; }
  .card-front .brand-dot { width: 44px; height: 44px; background: var(--teal); }
  .card-front .brand-name { color: var(--teal); font-size: 15px; letter-spacing: 0.5px; }

  .card-back .brand {
    left: 0; right: 0; top: 0; bottom: 0;
    flex-direction: column;
    justify-content: center;
    gap: 18px;
    text-align: center;
  }
  .card-back .brand-dot { width: 96px; height: 96px; background: var(--white); }
  .card-back .brand-name { color: var(--white); font-size: 17px; letter-spacing: 1px; }

  /* Contact block */
  .person {
    position: absolute;
    left: 32px;
    top: 292px;
    right: 20px;
  }
  .person-name {
    color: var(--teal);
    font-weight: 700;
    font-size: 16px;
    letter-spacing: 0.3px;
    line-height: 20px;
  }
  .person-credentials {
    color: var(--muted);
    font-size: 12.5px;
    line-height: 20px;
  }
  .person-title {
    color: var(--ink);
    font-size: 13px;
    line-height: 18px;
  }
  .address {
    margin-top: 12px;
    color: var(--ink);
    font-size: 13px;
    line-height: 18px;
    font-style: normal;
  }
  .contacts {
    list-style: none;
    margin-top: 10px;
    color: var(--ink);
    font-size: 13px;
    line-height: 18.5px;
  }
  .contacts li { display: flex; align-items: center; gap: 5px; white-space: nowrap; }
  .contacts .email { font-size: 10.6px; }
  .contacts svg { flex: none; width: 11px; height: 11px; fill: var(--teal); }
</style>
</head>
<body>
<main class="stage">

  <section class="card card-front" aria-label="Business card front">
    <div class="brand">
      <span class="brand-dot"></span>
      <span class="brand-name">Ridgeline<br>Pet Vision Care</span>
    </div>

    <div class="person">
      <h1 class="person-name">DELIA VOSSMAN</h1>
      <p class="person-credentials">BSC, DVM, MSC, DIPACVO</p>
      <p class="person-title">Veterinary Ophthalmologist</p>

      <address class="address">
        1874 Thornbury Rd<br>
        Kelowna, BC, V1X 4M9
      </address>

      <ul class="contacts">
        <li>
          <svg viewBox="0 0 12 12" aria-hidden="true"><path d="M1 4c0-2 1-3 5-3s5 1 5 3H8.5V3h-5v1zM2.5 5h7l1 6h-9z"/></svg>
          250.418.3927
        </li>
        <li class="email">
          <svg viewBox="0 0 12 12" aria-hidden="true"><path d="M1 2.5h10v7H1zM1.8 3.3 6 6.5l4.2-3.2"/><path d="M1.8 3.3 6 6.5l4.2-3.2" stroke="#fff" stroke-width="1" fill="none"/></svg>
          ridgelinepetvisioncare@mailbox-example.net
        </li>
        <li>
          <svg viewBox="0 0 12 12" aria-hidden="true"><circle cx="6" cy="6" r="5"/></svg>
          ridgelinepetvisioncare-example.net
        </li>
      </ul>
    </div>
  </section>

  <section class="card card-back" aria-label="Business card back">
    <div class="brand">
      <span class="brand-dot"></span>
      <span class="brand-name">Ridgeline<br>Pet Vision Care</span>
    </div>
  </section>

</main>
</body>
</html>
```